Business Card Design

New business card design

Target Market(s)

Residential & Commercial Property Managers

Industry/Entity Type

Plumbing Services

Contact Information for Business Card

Name - Rowan Keddle, title - Director, Phone Number - 0431 286 517, email - rowan@tbk-plumbing.com.au, Company ABN - 73 215 904 386,

Font styles to use
Sans Serif

Colors
0054AA
0677BA
7BADD7
CADEEF
E8F1F8

```html
<!DOCTYPE html>
<html lang="en">
<head>
<meta charset="utf-8">
<title>TBK Plumbing Services – Business Card</title>
<link rel="stylesheet" href="https://fonts.googleapis.com/css2?family=Poppins:wght@300;400;600&display=swap">
<style>
  :root{
    --stage:#212121;
    --paper:#ffffff;
    --navy:#1b2530;
    --taupe:#6e665b;
    --blue:#1fa3dd;
    --blue-deep:#0677ba;
    --blue-light:#7badd7;
    --grey-text:#7a7066;
  }
  *{margin:0;padding:0;box-sizing:border-box}
  html,body{width:1200px;height:780px;overflow:hidden;background:var(--stage)}
  body{font-family:"Poppins",sans-serif;position:relative}

  .card{position:absolute;top:225px;width:540px;height:330px;overflow:hidden;box-shadow:0 18px 40px rgba(0,0,0,.55)}
  .card--front{left:40px;background:var(--paper)}
  .card--back{left:620px}

  /* front: company name */
  .brand{position:absolute;top:62px;left:150px;display:flex;align-items:center;gap:14px}
  .brand__dot{width:16px;height:16px;border-radius:50%;background:var(--blue)}
  .brand__name{font-weight:300;font-size:27px;letter-spacing:.08em;color:var(--navy)}

  /* front: name band */
  .name-band{position:absolute;left:0;top:168px;width:270px;height:66px;background:var(--navy);
    display:flex;flex-direction:column;align-items:flex-end;justify-content:center;padding-right:40px}
  .name-band__name{font-size:24px;line-height:1.05;color:var(--blue);font-weight:300}
  .name-band__name strong{font-weight:600}
  .name-band__title{font-size:12px;color:#fff;font-weight:400;margin-top:2px}

  .band-marker{position:absolute;left:234px;top:176px;width:62px;height:62px;border-radius:50%;
    background:var(--blue);border:4px solid #fff;z-index:2}

  /* front: contact band */
  .contact-band{position:absolute;left:270px;right:0;top:200px;height:92px;background:var(--taupe);
    padding:12px 0 0 42px;display:flex;flex-direction:column;gap:4px}
  .contact-band__row{display:flex;align-items:center;gap:8px;color:#fff;font-size:13px;font-weight:300}
  .contact-band__icon{width:12px;height:12px;flex:none}

  .abn{position:absolute;left:72px;top:248px;font-size:12px;color:var(--blue);font-weight:300;letter-spacing:.02em}

  /* back: pattern area */
  .back-fill{width:100%;height:100%;background:linear-gradient(135deg,#1a8fcf 0%,var(--blue) 55%,#4bb8e8 100%)}
</style>
</head>
<body>
  <section class="card card--front">
    <div class="brand">
      <span class="brand__dot"></span>
      <span class="brand__name">TBK Plumbing Services</span>
    </div>

    <div class="name-band">
      <p class="name-band__name"><strong>Rowan</strong> Keddle</p>
      <p class="name-band__title">Director</p>
    </div>
    <span class="band-marker"></span>

    <div class="contact-band">
      <p class="contact-band__row">
        <svg class="contact-band__icon" viewBox="0 0 12 12"><path d="M3 1l2 2.5-1.2 1.2a6 6 0 0 0 3.5 3.5L8.5 7 11 9l-1.5 2A9 9 0 0 1 1 2.5z" fill="var(--blue)"/></svg>
        0431 286 517
      </p>
      <p class="contact-band__row">
        <svg class="contact-band__icon" viewBox="0 0 12 12"><circle cx="6" cy="6" r="5" fill="none" stroke="var(--blue)" stroke-width="1.3"/><path d="M1 6h10M6 1c-2.5 3-2.5 7 0 10M6 1c2.5 3 2.5 7 0 10" fill="none" stroke="var(--blue)" stroke-width="1"/></svg>
        www.tbk-plumbing.com.au
      </p>
      <p class="contact-band__row">
        <svg class="contact-band__icon" viewBox="0 0 12 12"><rect x="1" y="2.5" width="10" height="7" rx="1" fill="none" stroke="var(--blue)" stroke-width="1.3"/><path d="M1.5 3l4.5 3.5L10.5 3" fill="none" stroke="var(--blue)" stroke-width="1.2"/></svg>
        rowan@tbk-plumbing.com.au
      </p>
    </div>

    <p class="abn">ABN - 73 215 904 386</p>
  </section>

  <section class="card card--back">
    <div class="back-fill" role="img" aria-label="Repeating water-drop pattern in blue tones"></div>
  </section>
</body>
</html>
```